Non Profit Company Looking For New Website

The website for Fernvale Quillstone Heritage Society should offer the viewer beautiful photos that inspire condifence and joy and tap into our love of horses.

We would like to see a website that displays trust, quality and confidence. Needs to be responsive and mobile friendly for all browsers and coded for both Android & IOS.

READ ATTACHED WEBSITE TEMPLATE FOR COMPLETE DETAILS ON WHAT WE ARE LOOKING FOR.

Looking for recommmendations if we should use WordPress/WooCommerce for site or Wordpress with Shopify Plug in or just Shopify.

Must be both desktop and mobile friendly with fast page load speed. Need the ability to edit ourselves.

Industry/Entity Type

Non Profit

Coding

Coded - Design and coding required

Number of Pages Required

5+ page

Requirements
Must have
• We would like to see a website that displays trust, quality and confidence. Needs to be responsive and mobile friendly for all browsers and coded for both Android & IOS.

Looking for recommendations if we should use WordPress/WooCommerce for site or Wordpress with Shopify Plug in or just Shopify.

Logo Colour:
Pantone 7621 C

READ TEMPLATE THAT IS ATTACHED
Nice to have
• Like look of this website as a sample:
https://www.quellbrimtorva.com/

Another similar non profit organization
https://pellaworthcindle.com/

```html
<!DOCTYPE html>
<html lang="en">
<head>
<meta charset="utf-8">
<title>Fernvale Quillstone Heritage Society</title>
<link href="https://fonts.googleapis.com/css2?family=Cinzel:wght@400;600;700&family=Lato:ital,wght@0,400;0,700;1,400&display=swap" rel="stylesheet">
<style>
:root{
  --red:#9b111e;
  --red-dark:#7d0d17;
  --ink:#111;
  --white:#fff;
  --text:#3a3a3a;
  --footer:#1b1b1b;
}
*{margin:0;padding:0;box-sizing:border-box}
html,body{width:1200px;height:2985px;overflow:hidden;background:var(--white)}
body{position:relative;font-family:'Lato',sans-serif;color:var(--text)}
.abs{position:absolute}
.serif{font-family:'Cinzel',serif}

/* header */
.site-header{position:absolute;top:0;left:0;width:1200px;height:116px;background:var(--white);z-index:5}
.nav-link{position:absolute;top:58px;font-family:'Cinzel',serif;font-size:19px;letter-spacing:1px;color:var(--ink);text-decoration:none}
.nav-link.active{color:var(--red)}
.brand-plate{position:absolute;left:492px;top:0;width:216px;height:178px;z-index:6}
.brand-name{position:absolute;left:500px;top:30px;width:200px;text-align:center;font-family:'Cinzel',serif;font-weight:700;font-size:22px;line-height:30px;color:var(--red);z-index:7}
.brand-dot{position:absolute;left:588px;top:126px;width:24px;height:24px;border-radius:50%;background:var(--red);z-index:7}

/* hero */
.hero{position:absolute;top:116px;left:0;width:1200px;height:760px;background:linear-gradient(180deg,#5d86b3 0%,#a9c1d6 25%,#b98d60 45%,#6c8b3c 65%,#5b4433 90%)}
.hero-title{position:absolute;top:318px;left:0;width:1200px;text-align:center;font-family:'Cinzel',serif;font-size:82px;color:var(--white);letter-spacing:2px}
.hero-sub{position:absolute;top:408px;left:0;width:1200px;text-align:center;font-family:'Cinzel',serif;font-size:30px;line-height:50px;color:var(--white);letter-spacing:2px}
.btn{position:absolute;height:56px;border-radius:28px;font-family:'Cinzel',serif;font-size:17px;letter-spacing:1.5px;color:var(--white);display:flex;align-items:center;justify-content:center}
.btn-red{background:var(--red)}
.btn-black{background:var(--ink)}
.wave{position:absolute;left:0}

/* intro */
.section-title{position:absolute;left:0;width:1200px;text-align:center;font-family:'Cinzel',serif;font-weight:700;font-size:38px;color:var(--red);letter-spacing:1.5px}
.section-lead{position:absolute;left:200px;width:800px;text-align:center;font-style:italic;font-size:24px;line-height:42px;color:var(--text)}

/* about band */
.about-band{position:absolute;top:1115px;left:0;width:1200px;height:607px;background:var(--red)}
.about-title{position:absolute;left:78px;top:1214px;font-family:'Cinzel',serif;font-size:36px;line-height:42px;color:var(--white);letter-spacing:1.5px}
.about-copy{position:absolute;left:78px;top:1316px;width:480px;font-size:16.5px;line-height:29.6px;color:var(--white)}
.about-copy p+p{margin-top:7px}

/* contact */
.contact{position:absolute;top:2063px;left:0;width:1200px;height:730px;background:radial-gradient(ellipse at 30% 75%,#8a3a12 0%,#4a2414 40%,#2a1a14 75%)}
.contact-title{position:absolute;top:2190px;left:0;width:1200px;text-align:center;font-family:'Cinzel',serif;font-size:36px;color:var(--white);letter-spacing:1.5px}
.contact-sub{position:absolute;top:2256px;left:0;width:1200px;text-align:center;font-size:19px;color:var(--white)}
.info-icon{position:absolute;left:75px;width:61px;height:61px;border:2px solid var(--white);border-radius:50%;display:flex;align-items:center;justify-content:center}
.info-label{position:absolute;left:165px;font-family:'Cinzel',serif;font-size:21px;color:var(--white);letter-spacing:1px}
.info-value{position:absolute;left:165px;width:245px;font-weight:700;font-size:17px;line-height:28px;color:var(--white)}
.field{position:absolute;background:var(--white);border-radius:28px;font-size:17px;color:#222;padding:17px 28px}
.field.message{border-radius:24px}
.captcha{position:absolute;left:435px;top:2627px;width:343px;height:83px;background:#f9f9f9;border:1px solid #d3d3d3;border-radius:3px}
.captcha-box{position:absolute;left:15px;top:27px;width:30px;height:30px;border:2px solid #c1c1c1;border-radius:3px;background:var(--white)}
.captcha-text{position:absolute;left:57px;top:31px;font-size:16px;color:#222}
.captcha-mark{position:absolute;right:26px;top:18px;width:34px;height:34px;border-radius:50%;background:#c9d6ea}
.submit{position:absolute;left:947px;top:2642px;width:178px;height:55px;border-radius:28px;background:var(--red);font-family:'Cinzel',serif;font-size:20px;color:var(--white);letter-spacing:2px;display:flex;align-items:center;justify-content:center}

/* footer */
.site-footer{position:absolute;top:2793px;left:0;width:1200px;height:192px;background:var(--footer)}
.foot-link{position:absolute;top:2840px;font-family:'Cinzel',serif;font-size:19px;color:var(--white);letter-spacing:1px}
.copyright{position:absolute;top:2884px;left:0;width:1200px;text-align:center;font-size:15px;color:var(--white)}
.socials{position:absolute;top:2919px;left:515px;display:flex;gap:20px}
.socials span{width:18px;height:18px;border-radius:50%;background:var(--white)}
</style>
</head>
<body>

<header class="site-header">
  <a class="nav-link active" style="left:92px">Home</a>
  <a class="nav-link" style="left:201px">About</a>
  <a class="nav-link" style="left:316px">Adopt</a>
  <a class="nav-link" style="left:731px">Horses</a>
  <a class="nav-link" style="left:855px">Donate/Shop</a>
  <a class="nav-link" style="left:1041px">Contact</a>
</header>
<svg class="brand-plate" viewBox="0 0 216 178" aria-hidden="true"><path d="M0 0H216L188 178H28Z" fill="#fff"/></svg>
<div class="brand-name">Fernvale<br>Quillstone<br>Heritage</div>

<section class="hero" role="img" aria-label="Photo of a chestnut and white horse with a blond mane leaning over a wooden fence in a green paddock">
</section>
<h1 class="hero-title">Fernvale</h1>
<p class="hero-sub">We support and develop retired thoroughbred<br>racehorses for their next chapter in life</p>
<div class="btn btn-red" style="left:375px;top:535px;width:180px">ADOPT NOW</div>
<div class="btn btn-black" style="left:585px;top:535px;width:246px">MORE WAYS TO GIVE</div>

<svg class="wave" style="top:768px" width="1200" height="112" viewBox="0 0 1200 112" aria-hidden="true">
  <path d="M0 50 Q600 -30 1200 50 L1200 112 L0 112Z" fill="#fff"/>
  <path d="M0 58 Q600 -22 1200 58 L1200 105 Q600 -10 0 105Z" fill="#9b111e"/>
  <path d="M0 105 Q600 -10 1200 105 L1200 112 L0 112Z" fill="#fff"/>
</svg>

<h2 class="section-title" style="top:912px">Retire. Retrain. Rehome.</h2>
<p class="section-lead" style="top:973px">Fernvale Quillstone Heritage Society (FQHS) is a registered not-for-profit organization in Fernvale.</p>

<section class="about-band"></section>
<svg class="abs" style="left:588px;top:1136px" width="612" height="566" viewBox="0 0 612 566" role="img" aria-label="Photo of a young chestnut foal standing in golden hay in warm sunlight">
  <defs><linearGradient id="foal" x1="0" y1="0" x2="1" y2="1"><stop offset="0" stop-color="#e7b46a"/><stop offset=".5" stop-color="#b36a34"/><stop offset="1" stop-color="#6b3a1e"/></linearGradient></defs>
  <path d="M70 40 L612 0 L612 566 L60 530 Q0 524 0 470 L0 110 Q0 46 70 40Z" fill="url(#foal)"/>
</svg>
<h2 class="about-title">What is Thoroughbred<br>Aftercare?</h2>
<div class="about-copy">
  <p>The health, safety and welfare of our equine athletes does not end at the finish line, and retirement and aftercare are critical to the success of the racing industry.</p>
  <p>Aftercare is the safe placement of racehorses after their careers as racehorse are completed. Some horses might retire to the breeding shed or broodmare bands, while others are retrained for second careers.</p>
</div>
<div class="btn btn-black" style="left:78px;top:1561px;width:282px">LEARN MORE ABOUT US</div>

<h2 class="section-title" style="top:1776px">Adopt a Horse</h2>
<p class="section-lead" style="top:1837px">Fernvale Quillstone Heritage is committed to helping match you with the perfect horse.</p>
<div class="btn btn-black" style="left:374px;top:1947px;width:180px">ADOPT NOW</div>
<div class="btn btn-black" style="left:584px;top:1947px;width:246px">MORE WAYS TO GIVE</div>

<section class="contact" role="img" aria-label="Dim photo of a horse and rider silhouetted against a sunset"></section>
<svg class="wave" style="top:2008px" width="1200" height="112" viewBox="0 0 1200 112" aria-hidden="true">
  <path d="M0 0 H1200 V55 Q600 150 0 55Z" fill="#fff"/>
  <path d="M0 0 Q600 100 1200 0 L1200 55 Q600 150 0 55Z" fill="#fff"/>
  <path d="M0 0 Q600 125 1200 0 L1200 60 Q600 130 0 60Z" fill="#9b111e"/>
  <path d="M0 60 Q600 130 1200 60 L1200 66 Q600 140 0 66Z" fill="#fff"/>
</svg>

<h2 class="contact-title">Have a Question or Need More Information?</h2>
<p class="contact-sub">Give Us a Call or Use the Form Below</p>

<div class="info-icon" style="top:2377px"><svg width="22" height="26" viewBox="0 0 22 26"><path d="M11 0C5 0 1 4.5 1 10c0 7 10 16 10 16s10-9 10-16C21 4.5 17 0 11 0Zm0 14a4 4 0 1 1 0-8 4 4 0 0 1 0 8Z" fill="#9b111e"/></svg></div>
<div class="info-label" style="top:2370px">Location</div>
<div class="info-value" style="top:2396px">Neque porro quisquam est qui dolorem ipsum quia dolor</div>

<div class="info-icon" style="top:2480px"><svg width="22" height="22" viewBox="0 0 22 22"><path d="M5 1l4 5-2.5 2.5a12 12 0 0 0 7 7L16 13l5 4-2.5 3.5C10 21 1 12 1.5 3.5Z" fill="#9b111e"/></svg></div>
<div class="info-label" style="top:2480px">Phone</div>
<div class="info-value" style="top:2508px">1-800-234-5670</div>

<div class="info-icon" style="top:2580px"><svg width="24" height="18" viewBox="0 0 24 18"><rect width="24" height="18" rx="2" fill="#9b111e"/><path d="M1 2l11 8 11-8" stroke="#fff" stroke-width="1.6" fill="none"/></svg></div>
<div class="info-label" style="top:2584px">Email</div>
<div class="info-value" style="top:2612px">info@companyname.com</div>

<div class="field" style="left:433px;top:2323px;width:332px;height:55px">First Name</div>
<div class="field" style="left:794px;top:2323px;width:332px;height:55px">Last Name</div>
<div class="field" style="left:433px;top:2392px;width:332px;height:55px">Phone No</div>
<div class="field" style="left:794px;top:2392px;width:332px;height:55px">Email Address</div>
<div class="field message" style="left:433px;top:2464px;width:693px;height:146px">Message</div>

<div class="captcha"><span class="captcha-box"></span><span class="captcha-text">I'm not a robot</span><span class="captcha-mark"></span></div>
<div class="submit">SUBMIT</div>

<footer class="site-footer"></footer>
<span class="foot-link" style="left:232px">Home</span>
<span class="foot-link" style="left:341px">About</span>
<span class="foot-link" style="left:457px">Adopt</span>
<span class="foot-link" style="left:573px">Horses</span>
<span class="foot-link" style="left:697px">Donate/Shop</span>
<span class="foot-link" style="left:883px">Contact</span>
<p class="copyright">Copyright © 2021. Company Name. &nbsp; All Right Reserved</p>
<div class="socials"><span></span><span></span><span></span><span></span><span></span></div>

</body>
</html>
```